Wordpress Design Project

Hi,

I would like a more modern colourful design doing for my website ZAP Lnx (www.za%plnx.com - remove percentage). But I do still want to keep the same sort of colors, just maybe lighter. More interesting.

I want the inside pages to NOT all look the same with just boring text.

I want the site to look more appealing and maybe a new logo.
Updates

I would like to mention I would prefer to keep the same logo after rethinking it (possibly a slight refresh of the logo if you feel its a good idea) and the same color scheme as at present.

Saves us rebranding a lot of our apps, tools online ads etc.

Also I thought it is worth mentioning we have 2 parts to the site. The front end and the logged in area. It would be good if when making the front end you keep in mind the back end at http://p.za%plnx.com (remove percentage). We can only edit this limitedly (can edit the entire footer, the logo and full CSS of it). Would be good if we could make sure the header and footer can be used on the back end as well maybe to make it match.

I also want layouts making not just for the homepage. Obviously every page will basically be the same but I don't want all the other pages to just be 'text' and no real layout.

You can see out main pages on the website at the moment, I want those other pages to be laid out nice and differently as well. For example the testimonials page could be more interesting with speech bubbles and pictures of each person (just use placeholders). The affiliates page could be a description and then a nice fancy list of features why to join etc. 

Nothing overly complicated but I think it makes the whole site seem a lot better.

Target Market(s)

Affiliate Marketing. International.

Requirements
Must have
• Needs to be more room for links across the navigation at the top, also sub menus (at present we have a lot of pages which are hidden deep within other pages).
Nice to have
• Lists of features for advertisers and affiliates on the homepage part.

Menu items and buttons have nice hover over effects.

I want to get across on our pages all the different unique features we have.

Maybe some kind of slider which has past offer logos in, just use example logos.

```html
<!DOCTYPE html>
<html lang="en">
<head>
<meta charset="utf-8">
<title>ZAP Lnx – International Affiliate Network</title>
<link href="https://fonts.googleapis.com/css2?family=Carlito:wght@400;700&family=Open+Sans:wght@400;600&display=swap" rel="stylesheet">
<style>
:root{
  --blue:#1d6fa9;
  --blue-dark:#134a73;
  --blue-deep:#0f3f63;
  --blue-light:#2aa2d8;
  --orange:#f7941d;
  --orange-light:#ffb400;
  --white:#ffffff;
  --grey:#f3f3f3;
  --grey-text:#777;
  --nav-text:#555;
  --title:#1b6fa8;
}
*{margin:0;padding:0;box-sizing:border-box}
html,body{width:998px;height:1200px;overflow:hidden;background:#f5f5f5}
.page{position:relative;width:1200px;height:1443px;transform:scale(.83167);transform-origin:0 0;
  font-family:"Carlito",sans-serif;
  background:linear-gradient(var(--blue) 0 1267px,#efefef 1267px 1355px,#f7f7f7 1355px)}
.abs{position:absolute}
.glow{left:0;top:560px;width:1200px;height:286px;background:radial-gradient(ellipse at 55% 100%,#2cb0dc 0%,rgba(44,176,220,0) 65%)}
.divider{left:0;top:845px;width:1200px;height:2px;background:#3b8fc4}

.login{left:520px;top:0;width:565px;height:55px;background:var(--blue-deep);clip-path:polygon(0 0,100% 0,97% 100%,3% 100%);box-shadow:0 3px 6px rgba(0,0,0,.3)}
.login label{position:absolute;top:22px;color:#fff;font:12px "Open Sans",sans-serif}
.login .field{position:absolute;top:20px;height:20px;background:#0c3352;border:1px solid #0a2c47}
.btn-signin{left:452px;top:19px;width:75px;height:21px;background:var(--orange);color:#fff;font:700 13px "Carlito",sans-serif;text-align:center;line-height:21px;position:absolute}

.brand{left:130px;top:58px}
.brand-name{display:flex;align-items:center;gap:10px;color:var(--orange);font:700 46px "Carlito",sans-serif;line-height:1}
.brand-dot{width:14px;height:14px;border-radius:50%;background:var(--orange)}
.brand-tag{color:#fff;font:600 8px "Open Sans",sans-serif;letter-spacing:2px;margin-top:4px;margin-left:8px}

.phone{right:127px;top:74px;color:#fff;font:700 24px "Carlito",sans-serif;display:flex;align-items:center;gap:4px}
.search{left:824px;top:107px;width:246px;height:25px;background:var(--blue-deep);color:#8eb3cf;font:9px "Open Sans",sans-serif;padding:8px 8px}

.nav{left:130px;top:145px;width:941px;height:67px;background:linear-gradient(#fff,#e6e6e6);box-shadow:0 14px 14px -8px rgba(0,0,0,.35)}
.nav a{position:absolute;top:25px;color:var(--nav-text);font:17px "Carlito",sans-serif;text-decoration:none;text-transform:uppercase}
.nav a.active{color:var(--title)}

.slider{left:130px;top:252px;width:939px;height:303px;background:radial-gradient(ellipse at 40% 20%,#ffc400 0%,var(--orange) 55%,#f47c14 100%);overflow:hidden}
.slider-band{left:0;top:28px;width:939px;height:40px;background:linear-gradient(#4aa6dc,#1e6fa8)}
.band-text{left:449px;top:32px;color:#fff;font:italic 16px "Carlito",sans-serif;line-height:16px;text-align:right;width:222px}
.band-art{left:728px;top:18px;width:62px;height:62px;background:linear-gradient(#d8e9f6,#5b9dd0)}
.band-horn{left:380px;top:30px;width:48px;height:36px;background:linear-gradient(90deg,#f7941d,#ffd56a);border-radius:6px}
.crowd{left:45px;top:30px;width:300px;height:250px;background:linear-gradient(#e7c4a5,#c79b7a 55%,#7aa3c8);border-radius:40px 40px 4px 4px;opacity:.9}
.sign{left:112px;top:110px;width:170px;height:166px;background:#fff;text-align:center;padding-top:26px;font:700 23px "Carlito",sans-serif;line-height:32px;color:var(--title)}
.sign span{color:var(--orange);font-weight:400}
.slide-title{left:365px;top:95px;color:#fff;font:700 27px "Carlito",sans-serif;letter-spacing:-.5px}
.slide-copy{left:365px;top:128px;width:533px;color:#fff;font:12.5px "Open Sans",sans-serif;line-height:18px;text-align:justify}
.btn-dark{left:808px;top:236px;width:87px;height:25px;background:var(--blue-dark);color:#fff;font:12px "Open Sans",sans-serif;text-align:center;line-height:25px}
.dots{left:830px;top:274px;display:flex;gap:5px}
.dots i{width:12px;height:12px;border-radius:50%;background:#333}
.dots i:first-child{background:#fff}

.hero-photo{left:182px;top:575px;width:168px;height:270px;background:linear-gradient(#e9cc8e,#c9a071 35%,#5d8fb1 60%,#2d3238);border-radius:60px 60px 10px 10px}
.welcome-title{left:392px;top:592px;color:var(--orange);font:700 25px "Carlito",sans-serif;letter-spacing:-.3px}
.welcome-copy{left:392px;top:648px;width:619px;color:#fff;font:13px "Carlito",sans-serif;line-height:24px;text-align:justify}
.welcome-copy p+p{margin-top:10px}

.card{top:899px;width:299px;height:292px;background:var(--grey);box-shadow:0 1px 3px rgba(0,0,0,.2)}
.card h2{padding:18px 28px 10px;color:var(--title);font:700 24px "Carlito",sans-serif;border-bottom:1px solid #ddd}
.card .intro{padding:12px 13px 0 28px;color:var(--grey-text);font:10.5px "Open Sans",sans-serif;line-height:18px;text-align:justify}
.card h3{padding:12px 28px 6px;color:var(--title);font:18px "Carlito",sans-serif}
.card ul{list-style:none;padding-left:30px}
.card li{display:flex;align-items:center;gap:8px;height:34px;color:#444;font:10.5px "Open Sans",sans-serif}
.card li svg{flex:none}
.post-title{padding:8px 26px 0;color:var(--orange);font:18px "Carlito",sans-serif}
.post-meta{padding:2px 26px 0;color:#333;font:13px "Carlito",sans-serif}
.post-copy{padding:12px 14px 0 26px;color:var(--grey-text);font:10.5px "Open Sans",sans-serif;line-height:18px;text-align:justify}
.btn-light{top:1196px;width:86px;height:25px;background:var(--blue-light);color:#fff;font:11px "Open Sans",sans-serif;text-align:center;line-height:25px}

.app{top:1289px;width:143px;height:41px;background:#fff;border:1px solid #ddd;display:flex;align-items:center;gap:6px;padding:0 6px}
.app .ico{width:30px;height:30px;border-radius:6px;background:linear-gradient(#5ea9dd,#1f6fa8)}
.app b{display:block;color:var(--title);font:700 12px "Carlito",sans-serif}
.app small{display:block;color:var(--title);font:7px "Open Sans",sans-serif}
.follow{left:700px;top:1291px;width:236px;text-align:right;color:#555;font:9px "Open Sans",sans-serif}
.follow span{display:block;font:13px "Open Sans",sans-serif;margin-top:2px}
.social{top:1287px;width:32px;height:32px;color:#fff;font:700 8px "Carlito",sans-serif;display:flex;align-items:center;justify-content:center}

.footer-links{left:0;top:1373px;width:1200px;display:flex;justify-content:center;gap:0;color:#333;font:10.5px "Open Sans",sans-serif}
.footer-links a{color:#333;text-decoration:none;padding:0 13px}
.footer-links em{font-style:normal}
.copyright{left:0;top:1401px;width:1200px;text-align:center;color:#333;font:10.5px "Open Sans",sans-serif}
</style>
</head>
<body>
<div class="page">
  <div class="abs glow"></div>
  <div class="abs divider"></div>

  <form class="abs login">
    <label style="left:22px">E-mail :</label>
    <span class="field" style="left:65px;width:130px"></span>
    <label style="left:201px">Password :</label>
    <span class="field" style="left:261px;width:179px"></span>
    <span class="btn-signin">Sign In</span>
  </form>

  <div class="abs brand">
    <div class="brand-name">ZAP Lnx<span class="brand-dot"></span></div>
    <div class="brand-tag">EARN MONEY &amp; INCREASE SALES</div>
  </div>

  <div class="abs phone">
    <svg width="20" height="24" viewBox="0 0 20 24"><path d="M5 2l4 5-2 3c1 3 3 6 6 8l3-2 4 4-3 3C9 22 2 13 2 5z" fill="#fff"/></svg>
    +44 (0)1632 960418
  </div>
  <div class="abs search">Type search
    <svg class="abs" style="right:9px;top:8px" width="10" height="10" viewBox="0 0 10 10"><circle cx="4" cy="4" r="3" fill="none" stroke="#8eb3cf" stroke-width="1.4"/><path d="M6 6l3 3" stroke="#8eb3cf" stroke-width="1.6"/></svg>
  </div>

  <nav class="abs nav">
    <a class="active" style="left:41px">Home</a>
    <a style="left:140px">About Us</a>
    <a style="left:267px">Our Blog</a>
    <a style="left:396px">Testimonials</a>
    <a style="left:553px">Affiliates</a>
    <a style="left:683px">Advertisers</a>
    <a style="left:831px">Contact Us</a>
  </nav>

  <section class="abs slider">
    <div class="abs slider-band"></div>
    <div class="abs band-horn" role="img" aria-label="Megaphone illustration"></div>
    <div class="abs band-text">International Affiliate Network<br>Join Us Today!</div>
    <div class="abs band-art" role="img" aria-label="Dashboard screenshot illustration"></div>
    <div class="abs crowd" role="img" aria-label="Photo of a diverse group of smiling people"></div>
    <div class="abs sign"><span>ZAP Lnx:</span><br>International<br>CPA Affiliate<br>Network</div>
    <h1 class="abs slide-title">ZAP Lnx affiliate network.</h1>
    <p class="abs slide-copy">Lorem ipsum dolor sit amet, consectetur adipisicing elit, sed do eiusmod tempor incididunt ut labore et dolore magna aliqua. Ut enim ad minim veniam, quis nostrud exercitation ullamco laboris nisi ut aliquip ex ea commodo consequat.Lorem ipsum dolor sit amet, consectetur adipisicing elit, sed do eiusmod tempor incididunt ut labore et dolore magna aliqua. Ut enim ad minim veniam, quis nostrud exercitation ullamco laboris nisi ut aliquip ex ea commodo consequat.</p>
    <span class="abs btn-dark">Read More</span>
    <div class="abs dots"><i></i><i></i><i></i><i></i></div>
  </section>

  <div class="abs hero-photo" role="img" aria-label="Photo of a woman holding a laptop showing the brand name"></div>
  <h2 class="abs welcome-title">Welcome to the ZAP Lnx affiliate network.</h2>
  <div class="abs welcome-copy">
    <p>On time payments, hot &amp; exclusive CPL/CPA offers, fast support and low fees for advertisers, is the making of a leading affiliate network!</p>
    <p>ZAP Lnx offer a wide range of advertisers for your websites. So you can start monetizing your traffic or get an additional revenue stream, today.With the ZAP Lnx Affiliate Network we focus on lead generation offers. We have a range of competitions, surveys, incentives and gambling offers. Whatever the industry, you will be able to find offers to suit your traffic.ZAP Lnx is a powerful performance-based internet marketing network dedicated to advertisers to affiliates through its powerful affiliate network.</p>
  </div>

  <svg width="0" height="0" style="position:absolute"><defs>
    <symbol id="tick" viewBox="0 0 26 24"><rect x="1" y="6" width="17" height="17" fill="none" stroke="#f7941d" stroke-width="2"/><path d="M5 13l5 5L24 2" fill="none" stroke="#f7941d" stroke-width="3.5"/></symbol>
  </defs></svg>

  <article class="abs card" style="left:131px">
    <h2>Affiliates</h2>
    <p class="intro">Get access to a wide range of top performing offers for your websites and email marketing lists. Fresh and exclusive offers to promote. Join over 2,000 affiliates already signed up to ZAP Lnx.</p>
    <h3>Why they should join ?</h3>
    <ul>
      <li><svg width="28" height="24"><use href="#tick"/></svg>Erspiciatis unde omnis iste natus</li>
      <li><svg width="28" height="24"><use href="#tick"/></svg>Nemo enim ipsam voluptatem quia voluptas</li>
      <li><svg width="28" height="24"><use href="#tick"/></svg>Neque porro quisquam est, qui dolorem</li>
    </ul>
  </article>
  <article class="abs card" style="left:451px;width:298px">
    <h2 style="padding-left:21px">Advertisers</h2>
    <p class="intro" style="padding-left:21px">Generate sales/leads to your website instantly with the ZAP Lnx Affiliate Network. Only pay on performance, no m.onthly or setup fees. ZAP Lnx takes the risk out of advertising.</p>
    <h3 style="padding-left:15px">Why they should join ?</h3>
    <ul style="padding-left:22px">
      <li><svg width="28" height="24"><use href="#tick"/></svg>Erspiciatis unde omnis iste natus</li>
      <li><svg width="28" height="24"><use href="#tick"/></svg>Nemo enim ipsam voluptatem quia voluptas</li>
      <li><svg width="28" height="24"><use href="#tick"/></svg>Neque porro quisquam est, qui dolorem</li>
    </ul>
  </article>
  <article class="abs card" style="left:772px;width:298px">
    <h2 style="padding-left:26px">Recent Blog</h2>
    <h3 class="post-title">New Offers For China</h3>
    <p class="post-meta">Posted on May 1, 2013 by Maya</p>
    <p class="post-copy">Lorem ipsum dolor sit amet, consectetur adipisicing elit, sed do eiusmod tempor incididunt ut labore et dolore magna aliqua. Ut enim ad minim veniam, quis nostrud exercitation ullamco laboris nisi ut aliquip ex ea commodo consequat. Lorem ipsum dolor sit amet, consectetur adipisicing elit, sed do eiusmod Lorem ipsum dolor sit amet, consectetur adipisicing elit, sed do eiusmod</p>
  </article>
  <span class="abs btn-light" style="left:344px">Read More</span>
  <span class="abs btn-light" style="left:664px">Read More</span>
  <span class="abs btn-light" style="left:984px">Read More</span>

  <div class="abs app" style="left:134px"><span class="ico"></span><div><b>Mobile Stats</b><small>ZAP Lnx Mobile Website</small></div></div>
  <div class="abs app" style="left:314px"><span class="ico" style="border-radius:50%"></span><div><b>Orbit Browser</b><small>Official ZAP Lnx Extension</small></div></div>
  <div class="abs app" style="left:493px"><span class="ico" style="border-radius:50%;background:linear-gradient(#f7941d,#c85a12)"></span><div><b>Ember Browser</b><small>Official ZAP Lnx Extension</small></div></div>

  <div class="abs follow">You can follow us on social networking websites!<span>Use the buttons below.</span></div>
  <span class="abs social" style="left:952px;background:#3b5b99">Chatter</span>
  <span class="abs social" style="left:993px;background:#b22a22">Clipster</span>
  <span class="abs social" style="left:1031px;background:#2aa2d8">Chirpa</span>

  <div class="abs footer-links">
    <a>Home</a><em>|</em><a>About Us</a><em>|</em><a>Our Blog</a><em>|</em><a>Testimonials</a><em>|</em><a>Affliates</a><em>|</em><a style="padding-left:22px">Advertisers</a><em>|</em><a>Contact Us</a>
  </div>
  <div class="abs copyright">© 2013 ZAP Media UK Ltd - All Rights Reserved.</div>
</div>
</body>
</html>
```